Postcard for our major fundraising event - KindlingJOY2018

Bright Harbor KIDS Camp (BHK) and Youth Summit Trail Camp (YSTC) are ministries of Lindell Fellowship Church that serve Ventura County children of abuse, abandonment and neglect living in foster care. We are looking for a postcard design to promote our single largest fundraising event of the year, GatheringJOY2018, to raise awareness and support for children of abuse. GatheringJOY is a dinner banquet on at an exclusive outdoor venue, "Willow Hollow" with a rustic, ranch feel and with spectacular panoramic views of the City of Camarillo. The event will include music, refreshments, appetizers, a Santa Maria-style barbeque (BBQ), coffee and dessert, testimonials from camp, prize drawings, an opportunity to partner with BHK and YSTC, and time to socialize before and after.
Updates

I have just uploaded text copy to help designers come closer to what we are looking for. Thank you very much for your interest! -Rob

Target Market(s)

People from both within and from outside our sponsoring church who have a heart for hurting children and who are willing and able to financially support our camping (BHK & YSTC) ministries.

Industry/Entity Type

Church

Font styles to use
Serif
Decorative
Script

Requirements
Must have
• Name: GatheringJOY2018... raising awareness and support for children of abuse
• Date: Thursday, May 24, 2018, 6:30-8:00 pm
• Place: Willow Hollow at Dunmore Ranch, 2715 Barlow Lane, Somis, California.
• Cost: $30 per person
• Tickets: Available at Tixlane.com
• Front side should include the elements of the event (although not necessarily bulleted like below):
• • Social hour
• • Music
• • Hors d’eourves
• • Refreshments
• • Santa Maria-style BBQ dinner
• • Coffee & dessert
• • Prize drawings
• • Stories from camp
• See attachment for suggested copy for back side.
• BHK and YSTC logos should be included on the postcard. I’ve uploaded a variety of photos for the designer to choose from; they do not necessarily all have to be included. There are also lots more pics available on our Facebook (Bright Harbor KIDS of Ventura).
• The front-side of the postcard can be entirely images and text. The back-side of the post card should include our return address at the top left ("BHK/YSTC of Lindell Fellowship Church, 418 Kestrel Ridge Way, Ventura, CA 93017") and should leave at least the right half of the postcard clear for addressing and postage.
• BHK colors are purple (Pantone 267) and red (Pantone 186). YSTC colors are green and yellow.
Nice to have
• A selection of camp photos large enough to easily view, but no so many that they are too small to identify. And, perhaps, a design element that evokes a rustic, outdoors, western, ranch feel, but not so much that it seems that we are promoting a country hoedown.
Should not have
• Anything sexual or sensual, related to alcoholic beverages, gambling, guns, or anything negative.

```html
<!DOCTYPE html>
<html lang="en">
<head>
<meta charset="utf-8">
<title>GatheringJOY 2018 Postcard</title>
<link rel="stylesheet" href="https://fonts.googleapis.com/css2?family=Montserrat:wght@400;500;600;700&family=Dancing+Script:wght@500&display=swap">
<style>
  :root {
    --purple: #3b2a7a;
    --red: #d0202f;
    --white: #ffffff;
    --ink: #222222;
    --grey: #9a9a9a;
    --stage: #e7e7ea;
    --green: #4d8a3a;
    --yellow: #e7c93a;
  }
  * { margin: 0; padding: 0; box-sizing: border-box; }
  html, body { width: 1200px; height: 903px; overflow: hidden; }
  body { background: var(--stage); font-family: "Montserrat", sans-serif; color: var(--ink); position: relative; }

  .card { position: absolute; top: 265px; width: 560px; height: 373px; background: var(--white); overflow: hidden; border: 1px solid #d4d4d8; }
  .card--front { left: 30px; }
  .card--back { left: 610px; }
  .card svg.art { position: absolute; inset: 0; }

  .features { position: absolute; color: var(--white); font-size: 12px; line-height: 1.45; font-weight: 400; }
  .features--left { left: 22px; top: 150px; }
  .features--right { left: 150px; top: 150px; }
  .features li { list-style: none; margin-bottom: 3px; }

  .brand-row { position: absolute; left: 14px; top: 12px; width: 260px; display: flex; justify-content: space-between; align-items: center; }
  .brand { font-size: 11px; font-weight: 700; color: var(--purple); display: flex; align-items: center; gap: 5px; }
  .brand-dot { width: 16px; height: 16px; border-radius: 50%; background: var(--green); }
  .intro { position: absolute; left: 14px; top: 36px; width: 262px; text-align: center; font-size: 7.5px; font-weight: 600; line-height: 1.35; color: var(--purple); }
  .intro em { font-style: italic; font-weight: 500; }
  .title-band { position: absolute; left: 0; top: 76px; width: 280px; height: 28px; background: var(--red); color: var(--white); font-size: 19px; font-weight: 700; line-height: 28px; padding-left: 16px; letter-spacing: 0.3px; }
  .tagline { position: absolute; left: 10px; top: 106px; width: 268px; text-align: center; font-family: "Dancing Script", cursive; font-size: 11px; color: var(--ink); }
  .venue { position: absolute; left: 14px; top: 122px; width: 262px; text-align: center; color: var(--purple); font-size: 10.5px; font-weight: 600; line-height: 1.3; }
  .venue .exclusive { color: var(--red); font-style: italic; font-size: 9px; font-weight: 500; display: block; }
  .date-pill { display: inline-block; margin-top: 3px; background: var(--red); color: var(--white); border-radius: 3px; padding: 1px 8px; font-size: 11px; }
  .time { display: block; color: var(--ink); font-size: 11px; margin-top: 2px; }
  .tickets { position: absolute; left: 14px; top: 212px; width: 266px; display: flex; align-items: center; gap: 10px; }
  .price { border: 1px solid var(--grey); border-radius: 3px; padding: 2px 6px; font-size: 14px; font-weight: 600; color: var(--ink); position: relative; }
  .price b { color: var(--red); }
  .price-label { position: absolute; top: -10px; left: 40px; font-size: 8px; font-weight: 700; color: var(--red); background: var(--white); padding: 0 2px; }
  .availability { font-size: 9.5px; font-weight: 600; color: var(--ink); line-height: 1.2; }
  .availability span { color: var(--red); display: block; font-size: 10.5px; }
  .benefit { position: absolute; left: 14px; top: 244px; width: 266px; text-align: center; font-size: 8px; font-weight: 600; line-height: 1.3; color: var(--ink); }
  .benefit b { color: var(--red); }
  .contacts { position: absolute; left: 0; top: 276px; width: 286px; height: 97px; background: var(--purple); color: var(--white); padding: 8px 12px; font-size: 7.5px; line-height: 1.4; }
  .contacts-head { text-align: center; font-weight: 700; font-size: 8px; margin-bottom: 4px; }
  .contacts-grid { display: flex; justify-content: space-between; }
  .contact-label { color: #ff8a93; font-weight: 700; }
  .contact-name { font-weight: 600; }
  .contact-line { display: flex; align-items: center; gap: 3px; }
  .contact-line svg { width: 7px; height: 7px; flex: none; }

  .divider { position: absolute; left: 292px; top: 40px; width: 2px; height: 300px; background: var(--purple); }
  .return-address { position: absolute; left: 310px; top: 40px; font-size: 8px; line-height: 1.35; color: var(--ink); }
  .stamp-box { position: absolute; right: 24px; top: 60px; width: 64px; height: 56px; background: #d6d6d6; }
  .address-line { position: absolute; left: 318px; width: 216px; height: 1px; background: var(--grey); }
</style>
</head>
<body>

<section class="card card--front" aria-label="Postcard front">
  <svg class="art" viewBox="0 0 560 373" width="560" height="373">
    <defs>
      <linearGradient id="g-forest" x1="0" y1="0" x2="1" y2="1"><stop offset="0" stop-color="#5f9a3c"/><stop offset="1" stop-color="#2f6b2a"/></linearGradient>
      <linearGradient id="g-hall" x1="0" y1="0" x2="1" y2="1"><stop offset="0" stop-color="#c9b79a"/><stop offset="1" stop-color="#5c7f4a"/></linearGradient>
      <linearGradient id="g-lawn" x1="0" y1="0" x2="0" y2="1"><stop offset="0" stop-color="#5d7d3a"/><stop offset="1" stop-color="#8bb84e"/></linearGradient>
      <linearGradient id="g-craft" x1="0" y1="0" x2="1" y2="1"><stop offset="0" stop-color="#c98a9e"/><stop offset="1" stop-color="#2f5a3e"/></linearGradient>
    </defs>
    <polygon points="0,0 360,0 290,128 0,128" fill="url(#g-forest)" role="img" aria-label="Photo of campers on a ropes course among green trees"/>
    <polygon points="366,0 560,0 560,110 306,110" fill="url(#g-hall)" role="img" aria-label="Photo of a camp dinner party in a dining hall"/>
    <polygon points="303,116 470,116 330,373 162,373" fill="url(#g-lawn)" role="img" aria-label="Photo of kids doing archery on a lawn"/>
    <polygon points="476,116 560,116 560,373 336,373" fill="url(#g-craft)" role="img" aria-label="Photo of campers in sun hats at a craft table"/>
    <polygon points="0,134 287,134 187,316 0,316" fill="var(--purple)"/>
    <polygon points="0,322 184,322 170,348 0,348" fill="var(--red)"/>
  </svg>
  <ul class="features features--left">
    <li>Social hour</li>
    <li>Music</li>
    <li>Hors d’eourves</li>
    <li>Refreshments</li>
    <li>Coffee &amp; dessert</li>
  </ul>
  <ul class="features features--right">
    <li>Santa Maria-<br>style BBQ dinner</li>
    <li>Prize drawings</li>
    <li>Stories from<br>camp</li>
  </ul>
</section>

<section class="card card--back" aria-label="Postcard back">
  <div class="brand-row">
    <div class="brand">Bright Harbor KIDS</div>
    <div class="brand"><span class="brand-dot"></span>YSTC</div>
  </div>
  <p class="intro">Bright Harbor KIDS Camp &amp; Youth Summit Trail Camp<br>of Lindell Fellowship Church<br><em>invite you to join us for</em></p>
  <h1 class="title-band">GatheringJOY 2018</h1>
  <p class="tagline">raising awareness and support for children of abuse</p>
  <p class="venue">
    <span class="exclusive">at the exclusive</span>
    Willow Hollow at Dunmore Ranch<br>2715 Barlow Lane, Somis, CA<br>
    <span class="date-pill">Thursday, May 24, 2018</span>
    <span class="time">6:30-8:00 pm</span>
  </p>
  <div class="tickets">
    <div class="price"><span class="price-label">TICKETS:</span><b>$30</b> per person</div>
    <div class="availability">Available at<span>Tixlane.com</span></div>
  </div>
  <p class="benefit">All proceeds to benefit<br><b>BHKC &amp; YSTC serving children of abuse ages 7-14.</b></p>
  <div class="contacts">
    <p class="contacts-head">For more information:</p>
    <div class="contacts-grid">
      <div>
        <div class="contact-label">BHK:</div>
        <div class="contact-name">Rob Halvorsen (Director)</div>
        <div class="contact-line"><svg viewBox="0 0 10 10"><path d="M2 1l2 2-1 1.5c.6 1.2 1.3 1.9 2.5 2.5L7 6l2 2-1.5 1.5C4.5 9 1 5.5.5 2.5z" fill="#ff8a93"/></svg>(805) 555-0142</div>
        <div class="contact-line"><svg viewBox="0 0 10 10"><rect x="0.5" y="2" width="9" height="6" fill="#ff8a93"/></svg>bhkventura@mailbox.net</div>
      </div>
      <div>
        <div class="contact-label">YSTC:</div>
        <div class="contact-name">Dana Pruitt (Director)</div>
        <div class="contact-line"><svg viewBox="0 0 10 10"><path d="M2 1l2 2-1 1.5c.6 1.2 1.3 1.9 2.5 2.5L7 6l2 2-1.5 1.5C4.5 9 1 5.5.5 2.5z" fill="#ff8a93"/></svg>(805) 555-0187</div>
        <div class="contact-line"><svg viewBox="0 0 10 10"><rect x="0.5" y="2" width="9" height="6" fill="#ff8a93"/></svg>danapruittphoto@mailbox.net</div>
      </div>
    </div>
  </div>

  <div class="divider"></div>
  <address class="return-address" style="font-style:normal">BHK/YSTC of<br>Lindell Fellowship Church,<br>418 Kestrel Ridge Way,<br>Ventura, CA 93017</address>
  <div class="stamp-box"></div>
  <div class="address-line" style="top:190px"></div>
  <div class="address-line" style="top:228px"></div>
  <div class="address-line" style="top:266px"></div>
</section>

</body>
</html>
```